RW Holloway LLC Business Card - Civil Engineering & Consulting Firm

We need a Business Card that is elegant, and masculine.  It is our Professional Civil Engineering & Consulting Company located in San Antonio TX (Not s construction or builder firm- no gears & no tool images please). We provide civil engineering services including  commercial site plans, grading and drainage plans, utility plans, hydraulics and hydrology, land planning, utility coordination, and other general civil engineering services related to commercial and residential development.
We have 2 existing Logos. We would like to convey reliability, strength, trustworthiness and attention to detail.  Blues and orange tones as per logo We are OK with the use of a darker blue in the mix.  We have 2 logo versions - Full Company Name Logo to go on the back of card, & Small Icon Logo for the front w/ personal Info.

Target Market(s)
Architects, Real Estate Developers, Other Strctural Engineers, Surveyers, General Contractors
Industry/Entity Type
Professional Civil Engineering
Contact Information for Business Card
Name, Position, Address, Cell & Office #, email, and company website
Font styles to use
Other font styles liked:
- Avian
Requirements
Should not have
- No Tools, No Gears, no Cranes, or Construction Equipment.

```html
<!DOCTYPE html>
<html lang="en">
<head>
<meta charset="utf-8">
<title>RW Holloway LLC Business Card</title>
<link rel="stylesheet" href="https://fonts.googleapis.com/css2?family=Montserrat:wght@300;400;600;700&display=swap">
<style>
  :root {
    --backdrop: #c9c9c9;
    --card-white: #ffffff;
    --card-fade: #f1eeee;
    --sky-blue: #79acd6;
    --steel-blue: #7f9db8;
    --accent-orange: #e8922f;
    --ink: #1d1d1d;
    --paper-text: #ffffff;
  }
  html, body {
    margin: 0;
    padding: 0;
    width: 1200px;
    height: 813px;
    overflow: hidden;
    background: var(--backdrop);
    font-family: "Montserrat", sans-serif;
  }
  .canvas {
    position: relative;
    width: 1200px;
    height: 813px;
  }
  .card {
    position: absolute;
    top: 254px;
    width: 530px;
    height: 305px;
    overflow: hidden;
    box-shadow: 0 10px 30px rgba(0,0,0,0.35);
  }
  /* Front card */
  .card-front {
    left: 45px;
    background: linear-gradient(120deg, var(--card-white) 45%, var(--card-fade) 100%);
  }
  .front-sweep {
    position: absolute;
    inset: 0;
    width: 100%;
    height: 100%;
  }
  .front-mark {
    position: absolute;
    top: 38px;
    right: 150px;
    display: flex;
    align-items: center;
    gap: 8px;
    font-weight: 600;
    font-size: 15px;
    color: var(--accent-orange);
  }
  .front-mark .mark-square {
    width: 12px;
    height: 12px;
    background: var(--accent-orange);
  }
  .contact-block {
    position: absolute;
    left: 34px;
    top: 118px;
    color: var(--ink);
    font-size: 12.5px;
    line-height: 1.3;
  }
  .person-name {
    margin: 0;
    font-size: 16px;
    font-weight: 700;
    letter-spacing: 0.5px;
    color: var(--accent-orange);
    text-transform: uppercase;
  }
  .person-role {
    margin: 0 0 10px;
  }
  .address {
    margin: 0 0 10px;
    font-style: normal;
  }
  .contact-list {
    list-style: none;
    margin: 0;
    padding: 0;
  }
  .contact-list li {
    display: flex;
    align-items: center;
    gap: 8px;
    margin-bottom: 3px;
  }
  .contact-icon {
    width: 15px;
    height: 15px;
    flex: none;
  }
  /* Back card */
  .card-back {
    left: 625px;
    background: linear-gradient(170deg, #7d9fbc 0%, #9fa0a4 38%, #c5a07d 65%, #e29448 100%);
  }
  .back-facets {
    position: absolute;
    inset: 0;
    width: 100%;
    height: 100%;
  }
  .back-name {
    position: absolute;
    left: 0;
    right: 0;
    top: 120px;
    text-align: center;
    font-weight: 300;
    font-size: 40px;
    letter-spacing: 4px;
    color: var(--paper-text);
    text-transform: uppercase;
  }
  .back-rule {
    position: absolute;
    left: 110px;
    right: 110px;
    top: 180px;
    height: 2px;
    background: var(--paper-text);
  }
</style>
</head>
<body>
<main class="canvas">

  <section class="card card-front" aria-label="Business card front">
    <svg class="front-sweep" viewBox="0 0 530 305" preserveAspectRatio="none" aria-hidden="true">
      <defs>
        <linearGradient id="sweep-fill" x1="0" y1="0" x2="0" y2="1">
          <stop offset="0" stop-color="#79acd6"/>
          <stop offset="0.6" stop-color="#a9b2b8"/>
          <stop offset="1" stop-color="#e8922f"/>
        </linearGradient>
      </defs>
      <path d="M430 0 C420 120 360 230 230 305 L530 305 L530 0 Z" fill="url(#sweep-fill)"/>
      <path d="M408 0 C400 120 340 225 205 305" fill="none" stroke="#79acd6" stroke-width="4"/>
    </svg>

    <div class="front-mark">
      <span class="mark-square" aria-hidden="true"></span>
      <span>RW Holloway LLC</span>
    </div>

    <div class="contact-block">
      <h1 class="person-name">Dana Whitfield</h1>
      <p class="person-role">Co-Founder</p>
      <address class="address">4180 N. Cedar Ridge Road<br>Suite 210 Alamo Hts</address>
      <ul class="contact-list">
        <li>
          <svg class="contact-icon" viewBox="0 0 16 16" aria-hidden="true"><circle cx="8" cy="8" r="8" fill="#e8922f"/><path d="M5 4.5l1.6-.5 1 2-1 .8a5 5 0 0 0 2.6 2.6l.8-1 2 1-.5 1.6c-3.3.2-6.7-3.2-6.5-6.5z" fill="#fff"/></svg>
          555-014-2280
        </li>
        <li>
          <svg class="contact-icon" viewBox="0 0 16 16" aria-hidden="true"><circle cx="8" cy="8" r="8" fill="#e8922f"/><rect x="4.5" y="7" width="7" height="4.5" rx="1" fill="#fff"/><path d="M4 6.5c2-2 6-2 8 0" stroke="#fff" stroke-width="1.4" fill="none"/></svg>
          555-014-2291
        </li>
        <li>
          <svg class="contact-icon" viewBox="0 0 16 16" aria-hidden="true"><circle cx="8" cy="8" r="8" fill="#e8922f"/><rect x="4" y="5" width="8" height="6" fill="#fff"/><path d="M4 5l4 3.5L12 5" stroke="#e8922f" stroke-width="1" fill="none"/></svg>
          info@rwhollowayllc
        </li>
        <li>
          <svg class="contact-icon" viewBox="0 0 16 16" aria-hidden="true"><circle cx="8" cy="8" r="8" fill="#e8922f"/><circle cx="8" cy="8" r="4" fill="none" stroke="#fff" stroke-width="1"/><path d="M4 8h8M8 4c-2 2.5-2 5.5 0 8M8 4c2 2.5 2 5.5 0 8" stroke="#fff" stroke-width="0.8" fill="none"/></svg>
          www.rwhollowayeng.com
        </li>
      </ul>
    </div>
  </section>

  <section class="card card-back" aria-label="Business card back">
    <svg class="back-facets" viewBox="0 0 530 305" preserveAspectRatio="none" aria-hidden="true">
      <path d="M0 0 L260 0 L120 305 L0 305 Z" fill="#ffffff" opacity="0.06"/>
      <path d="M330 0 L530 0 L530 200 Z" fill="#ffffff" opacity="0.05"/>
      <path d="M200 305 L530 120 L530 305 Z" fill="#000000" opacity="0.04"/>
    </svg>
    <div class="back-name">RW Holloway LLC</div>
    <div class="back-rule" aria-hidden="true"></div>
  </section>

</main>
</body>
</html>
```